Company raising consciousness thru leadership & self-awareness needs amazing Letterhead

We are a technology company that spun out of a consulting firm. We are waking people up in corporate America through surveys, leadership development, workshops and consulting. Getting employees to become self-aware and changing company culture through improved leadership and team effectiveness. We need Word letterhead for our proposals, handouts, and worksheets that match our brand standard, is fresh, and communicates trust, credibility and professionalism.

Our target clients are other businesses, and executive leaders and C-suite leaders in those companies.

Sans Serif

• A Word template we can use for handouts, proposals, executive summary, project management documents, and letters. We need our logo. Please add page number and date on the footer. Must match the theme of our new website in look and feel to match the brand we are trying to promote. Use the colors from our brand standard document I submitted.

```html
<!DOCTYPE html>
<html lang="en">
<head>
<meta charset="utf-8">
<title>Aurense Letterhead</title>
<link href="https://fonts.googleapis.com/css2?family=Lato:wght@400;700;900&display=swap" rel="stylesheet">
<style>
  :root {
    --backdrop: #c9bfbc;
    --paper: #fdfdfb;
    --navy: #1f3a78;
    --sky: #27a6dc;
    --violet: #7b3fa0;
    --ink: #2a3f7a;
    --rule: #9aa3c0;
    --watermark: #eef1f7;
  }
  * { margin: 0; padding: 0; box-sizing: border-box; }
  html, body { width: 1200px; height: 784px; overflow: hidden; }
  body {
    background: var(--backdrop);
    font-family: "Lato", sans-serif;
    position: relative;
  }
  .letterhead {
    position: absolute;
    left: 338px;
    top: 22px;
    width: 524px;
    height: 740px;
    background: var(--paper);
    box-shadow: 0 6px 18px rgba(0,0,0,0.18);
    overflow: hidden;
  }
  .brand {
    position: absolute;
    left: 38px;
    top: 40px;
    display: flex;
    align-items: center;
    gap: 10px;
  }
  .brand-dot {
    width: 18px; height: 18px;
    border-radius: 50%;
    background: var(--violet);
  }
  .brand-name {
    font-weight: 900;
    font-size: 30px;
    letter-spacing: 1px;
    color: var(--navy);
  }
  .date-field {
    position: absolute;
    right: 40px;
    top: 150px;
    font-size: 10px;
    color: var(--ink);
    display: flex;
    align-items: flex-end;
    gap: 3px;
  }
  .blank { display: inline-block; border-bottom: 1px solid var(--ink); width: 22px; height: 10px; }
  .watermark {
    position: absolute;
    left: 112px;
    top: 210px;
    width: 300px;
    height: 300px;
    border-radius: 50%;
    border: 10px solid var(--watermark);
  }
  .page-field {
    position: absolute;
    left: 26px;
    bottom: 40px;
    font-size: 10px;
    color: var(--ink);
    display: flex;
    align-items: flex-end;
    gap: 4px;
  }
  .page-field .blank { width: 56px; }
  .footer-contact {
    position: absolute;
    left: 258px;
    bottom: 32px;
    display: flex;
    align-items: flex-start;
    gap: 12px;
  }
  .footer-dot {
    width: 34px; height: 34px;
    border-radius: 50%;
    border: 3px solid var(--violet);
    margin-top: 4px;
  }
  .footer-divider {
    width: 1px;
    height: 82px;
    background: var(--rule);
  }
  .contact-list {
    list-style: none;
    font-size: 11px;
    line-height: 16px;
    color: var(--ink);
  }
  .contact-list li { display: flex; align-items: center; gap: 6px; }
  .contact-list .plain { padding-left: 16px; }
  .contact-list svg { width: 10px; height: 10px; flex: none; }
  .edge-band {
    position: absolute;
    left: 0; right: 0; bottom: 0;
    height: 14px;
  }
</style>
</head>
<body>
  <main class="letterhead">
    <header class="brand">
      <span class="brand-dot"></span>
      <span class="brand-name">AURENSE</span>
    </header>

    <div class="date-field">Date: <span class="blank"></span>/<span class="blank"></span>/<span class="blank"></span></div>

    <div class="watermark" aria-hidden="true"></div>

    <div class="page-field">Page: <span class="blank"></span></div>

    <footer class="footer-contact">
      <span class="footer-dot"></span>
      <span class="footer-divider"></span>
      <ul class="contact-list">
        <li class="plain">1234 First Line Address</li>
        <li class="plain">5678 Second Line Address</li>
        <li>
          <svg viewBox="0 0 10 10"><path d="M2 1 L4 1 L4.6 3 L3.4 3.8 Q4.4 5.8 6.2 6.6 L7 5.4 L9 6 L9 8 Q5 9 2.2 6 Q0.8 3.6 2 1Z" fill="var(--violet)"/></svg>
          (111) 999-0000
        </li>
        <li>
          <svg viewBox="0 0 10 10"><rect x="0.5" y="2" width="9" height="6.5" fill="var(--violet)"/><path d="M0.5 2 L5 5.6 L9.5 2" stroke="#fff" stroke-width="0.8" fill="none"/></svg>
          info@yourmail.com
        </li>
        <li>
          <svg viewBox="0 0 10 10"><circle cx="5" cy="5" r="4.3" fill="var(--violet)"/><path d="M0.8 5 H9.2 M5 0.8 V9.2 M5 0.8 Q2.4 5 5 9.2 M5 0.8 Q7.6 5 5 9.2" stroke="#fff" stroke-width="0.6" fill="none"/></svg>
          www.yourwebsite.com
        </li>
      </ul>
    </footer>

    <svg class="edge-band" viewBox="0 0 524 14" preserveAspectRatio="none" aria-hidden="true">
      <polygon points="0,0 232,0 224,14 0,14" fill="var(--sky)"/>
      <polygon points="238,0 524,0 524,14 230,14" fill="var(--navy)"/>
    </svg>
  </main>
</body>
</html>
```